Update informational website

I need a new modern site design for my website.

Here is the site: http://q.zq/kpTr

Here is a theme I liked: http://q.zq/kpTm

I am looking for something with clean lines and an exciting designs and graphics, please use images from brindlecove.com and track the images used so I can buy them if I like the design.

I just need the homepage and one interior page designed.

Colors
Bright Green #6ed30d
Dark Text #222
Lighter Text #444

Number of Pages Required

2 page

Font styles to use
Sans Serif

Requirements
Must have
• Clean, good spacing, responsive design, high resolution design

```html
<!DOCTYPE html>
<html lang="en">
<head>
<meta charset="utf-8">
<title>Verdant Tint – Window Film Services</title>
<link rel="stylesheet" href="https://fonts.googleapis.com/css2?family=Questrial&family=Open+Sans:wght@400;600&display=swap">
<style>
  :root{
    --green:#6ed30d;
    --green-deep:#4fa607;
    --green-light:#8fe33a;
    --text-dark:#222;
    --text-light:#444;
    --muted:#8a8a8a;
    --white:#fff;
    --card-dark:#262626;
    --field:#f2f2f2;
    --field-line:#dcdcdc;
  }
  *{box-sizing:border-box;margin:0;padding:0}
  html,body{width:1200px;height:4235px;overflow:hidden;background:var(--white)}
  body{position:relative;font-family:"Open Sans",Arial,sans-serif;color:var(--text-light)}
  .abs{position:absolute}

  /* Hero */
  .hero{left:0;top:0;width:1200px;height:690px;
    clip-path:polygon(0 0,100% 0,100% 595px,50% 690px,0 595px);
    background:linear-gradient(180deg,#6e6d6b 0%,#8a8784 32%,#4c4846 62%,#1e1c1c 100%)}
  .topbar{left:0;top:0;width:1200px;height:45px;background:rgba(0,0,0,.35);color:var(--white);font-size:12px}
  .topbar .call{left:133px;top:14px;display:flex;align-items:center;gap:8px}
  .topbar .socials{right:133px;top:15px;display:flex;gap:14px}
  .topbar .socials span{width:14px;height:14px;border-radius:50%;border:1.5px solid var(--white)}
  .brand{left:133px;top:80px;font-family:"Questrial",Arial,sans-serif;font-size:34px;color:var(--green);line-height:1}
  .nav{right:133px;top:96px;display:flex;gap:30px;font-family:"Questrial",Arial,sans-serif;font-size:13px;color:var(--white);text-transform:uppercase}
  .nav .active{border-bottom:2px solid var(--green);padding-bottom:4px}
  .arrow{top:292px;width:28px;height:36px;background:rgba(255,255,255,.25);display:flex;align-items:center;justify-content:center}
  .hero-kicker{left:133px;top:434px;font-family:"Questrial",Arial,sans-serif;font-size:36px;line-height:1;color:var(--white)}
  .hero-title{left:133px;top:482px;font-family:"Questrial",Arial,sans-serif;font-size:36px;line-height:1;color:var(--white);letter-spacing:1px}
  .btn{background:var(--green);color:var(--white);font-family:"Questrial",Arial,sans-serif;font-size:13px;text-transform:uppercase;display:flex;align-items:center;justify-content:center;gap:8px;
    clip-path:polygon(10px 0,100% 0,calc(100% - 10px) 100%,0 100%)}
  .hero-btn{left:133px;top:528px;width:144px;height:40px}

  /* Section titles */
  .title{left:0;width:1200px;text-align:center;font-family:"Questrial",Arial,sans-serif;font-size:34px;color:var(--green);text-transform:uppercase;line-height:1}
  .subtitle{left:0;width:1200px;text-align:center;font-family:"Questrial",Arial,sans-serif;font-size:14px;color:var(--text-dark);text-transform:uppercase;letter-spacing:.5px}
  .rule{left:560px;width:80px;height:3px;background:var(--text-dark)}
  .on-green .title,.on-green .subtitle{color:var(--white)}
  .intro{left:133px;top:872px;width:934px;text-align:center;font-size:12.5px;line-height:23px;color:var(--text-light)}

  /* Green bands */
  .band{left:0;width:1200px;
    background:linear-gradient(160deg,var(--green-light) 0%,var(--green) 40%,var(--green-deep) 100%)}
  .band-services{top:988px;height:726px;
    clip-path:polygon(0 0,50% 127px,100% 0,100% 593px,50% 726px,0 593px)}
  .band-reviews{top:2395px;height:725px;
    clip-path:polygon(0 0,50% 118px,100% 0,100% 598px,50% 725px,0 598px)}

  .services{left:133px;top:1307px;width:934px;height:226px;display:flex;gap:3px}
  .service{flex:1;background:var(--card-dark);color:var(--white);padding:26px 18px 0}
  .service h3{font-family:"Questrial",Arial,sans-serif;font-weight:400;font-size:20px;line-height:23px;text-transform:uppercase;margin-top:18px}
  .service p{font-size:10px;color:#9a9a9a;margin-top:10px}

  /* Gallery */
  .ph-showroom{left:133px;top:1898px;width:460px;height:361px;background:linear-gradient(120deg,#dfe6ec 0%,#f7f8fa 40%,#c9d2da 100%)}
  .ph-taillight{left:601px;top:1898px;width:229px;height:177px;background:linear-gradient(135deg,#b5121b,#e8343c 55%,#6d6d6d)}
  .ph-silver{left:838px;top:1898px;width:229px;height:177px;background:linear-gradient(180deg,#f3d9a4,#c9a56b 55%,#7b6a55)}
  .ph-factory{left:601px;top:2083px;width:229px;height:176px;background:linear-gradient(180deg,#7d8fa0,#dfe5ea 70%,#b7c1ca)}
  .ph-blue{left:838px;top:2083px;width:229px;height:176px;background:linear-gradient(135deg,#2b78a8,#7fc1e3 55%,#1a4a6b)}
  .dots{left:0;width:1200px;display:flex;justify-content:center;gap:8px}
  .dots span{width:12px;height:12px;border-radius:50%;background:#c4c4c4}
  .dots span.on{background:var(--green)}
  .on-green .dots span{background:#3b3b3b}
  .on-green .dots span.on{background:var(--white)}

  /* Testimonials */
  .review{top:2711px;width:296px;height:226px;background:var(--white);padding:22px 20px 0}
  .review p{font-size:11px;line-height:17px;color:var(--text-light)}
  .reviewer{position:absolute;left:20px;top:150px;display:flex;align-items:center;gap:14px}
  .avatar{width:44px;height:44px;border-radius:50%;background:linear-gradient(135deg,#d8c6b5,#8f7c6b)}
  .reviewer b{display:block;font-family:"Questrial",Arial,sans-serif;font-weight:400;font-size:20px;color:var(--text-dark);text-transform:uppercase;line-height:1}
  .reviewer small{font-size:10px;color:var(--muted);text-transform:uppercase}

  /* Contact form */
  .field{height:40px;background:var(--field);border:1px solid var(--field-line);font-size:11px;color:var(--muted);padding:12px 14px}
  .submit{left:553px;top:3426px;width:97px;height:40px}

  /* Dark contact band */
  .band-dark{left:0;top:3496px;width:1200px;height:570px;
    background:linear-gradient(180deg,#2a2a2a,#3d3d3d 50%,#252525);
    clip-path:polygon(0 0,50% 133px,100% 0,100% 444px,50% 570px,0 444px)}
  .info-row{left:133px;top:3814px;width:934px;display:flex;justify-content:space-between;color:var(--white);font-size:16px}
  .info-row div{display:flex;align-items:center;gap:10px}
  .social-row{left:0;top:3880px;width:1200px;display:flex;justify-content:center;gap:12px}
  .social-row span{width:34px;height:34px;border-radius:50%;border:1.5px solid var(--white)}

  .footer-links{left:0;top:4138px;width:1200px;text-align:center;font-size:12px;color:var(--text-light)}
  .footer-links span{margin:0 8px;color:#aaa}
  .copyright{left:0;top:4172px;width:1200px;text-align:center;font-size:12px;color:var(--text-light)}
</style>
</head>
<body>

<!-- Hero -->
<section class="abs hero" role="img" aria-label="Hero photograph: sports sedan driving on a highway"></section>

<div class="abs topbar">
  <div class="abs call">
    <svg width="12" height="12" viewBox="0 0 24 24"><path fill="#fff" d="M6.6 10.8a15 15 0 0 0 6.6 6.6l2.2-2.2c.3-.3.7-.4 1-.2 1.1.4 2.3.6 3.6.6.6 0 1 .4 1 1V20c0 .6-.4 1-1 1A17 17 0 0 1 3 4c0-.6.4-1 1-1h3.5c.6 0 1 .4 1 1 0 1.3.2 2.5.6 3.6.1.3 0 .7-.2 1z"/></svg>
    Call us on : 480.555.0142
  </div>
  <div class="abs socials"><span></span><span></span><span></span><span></span><span></span><span></span></div>
</div>

<div class="abs brand">Verdant Tint</div>
<nav class="abs nav">
  <span class="active">Home</span><span>Window Film Services</span><span>Film</span><span>About</span><span>Gallery</span><span>Contact</span>
</nav>

<div class="abs arrow" style="left:40px"><svg width="10" height="14" viewBox="0 0 10 14"><path d="M8 1 2 7l6 6" stroke="#fff" stroke-width="2" fill="none"/></svg></div>
<div class="abs arrow" style="right:40px"><svg width="10" height="14" viewBox="0 0 10 14"><path d="m2 1 6 6-6 6" stroke="#fff" stroke-width="2" fill="none"/></svg></div>

<div class="abs hero-kicker">Maecenas vel tortor</div>
<div class="abs hero-title">ACCUMSAN QUAM VARIUS</div>
<div class="abs btn hero-btn">Read more
  <svg width="8" height="10" viewBox="0 0 8 10"><path d="m2 1 4 4-4 4" stroke="#fff" stroke-width="2" fill="none"/></svg>
</div>

<!-- Welcome -->
<h1 class="abs title" style="top:780px">Welcome to</h1>
<div class="abs subtitle" style="top:818px">Verdant Tint</div>
<div class="abs rule" style="top:845px"></div>
<p class="abs intro">Nullam lorem urna, tempus eget mollis et, dapibus ac sem. Suspendisse gravida ornare erat sed pulvinar. Vestibulum luctus ex in egestas fringilla. Fusce nec leo ac urna pulvinar auctor. Mauris bibendum fringilla velit. Nulla in lorem at massa pellentesque posuere. Nulla tristique posuere molestie. Aliquam erat volutpat. Etiam quis aliquet risus. Duis ornare erat eget magna dapibus, in accumsan quam pharetra. Nam tempus, quam in bibendum vulputate, sapien dolor viverra nisl, vitae euismod elit turpis et nulla. Aliquam erat volutpat. Pellentesque blandit lacus eget nunc faucibus, et tincidunt eros viverra.</p>

<!-- Services -->
<section class="abs band band-services" role="img" aria-label="Green tinted background photo of a car wheel"></section>
<div class="on-green">
  <h2 class="abs title" style="top:1194px">What we do</h2>
  <div class="abs subtitle" style="top:1232px">Services</div>
  <div class="abs rule" style="top:1258px"></div>
</div>
<div class="abs services">
  <div class="service">
    <svg width="56" height="44" viewBox="0 0 56 44" fill="none" stroke="#fff" stroke-width="2.5"><path d="M4 40V16L18 4h32v36z"/><path d="M8 18 20 8h26v12H8z"/><path d="M38 26h6"/></svg>
    <h3>Automotive<br>Film</h3>
    <p>Heat, Infrared, and UV protection</p>
  </div>
  <div class="service">
    <svg width="56" height="44" viewBox="0 0 56 44" fill="none" stroke="#fff" stroke-width="2.5"><path d="M16 4h24l6 16v18H10V20z"/><path d="M14 20h28"/><circle cx="18" cy="29" r="3"/><circle cx="38" cy="29" r="3"/></svg>
    <h3>Commercial &amp;<br>Residential</h3>
    <p>Your Valley Commercial Film Experts</p>
  </div>
  <div class="service">
    <svg width="56" height="44" viewBox="0 0 56 44" fill="none" stroke="#fff" stroke-width="2.5"><path d="M6 36V22l6-14h32l6 14v14z"/><path d="M10 22h36"/><circle cx="16" cy="29" r="3"/><circle cx="40" cy="29" r="3"/><path d="M6 36v5M50 36v5"/></svg>
    <h3>Clear Bra</h3>
    <p>Protect Your Paint</p>
  </div>
  <div class="service">
    <svg width="64" height="44" viewBox="0 0 64 44" fill="none" stroke="#fff" stroke-width="2.5"><path d="M4 32V22l10-12h24l14 10 8 2v10z"/><circle cx="16" cy="32" r="5" fill="#262626"/><circle cx="48" cy="32" r="5" fill="#262626"/></svg>
    <h3>Vehicle Wraps</h3>
    <p>An easy solution to a boring car</p>
  </div>
</div>

<!-- Gallery -->
<h2 class="abs title" style="top:1790px">Gallery</h2>
<div class="abs subtitle" style="top:1829px">Vestibulum condimentum</div>
<div class="abs rule" style="top:1856px"></div>
<div class="abs ph-showroom" role="img" aria-label="Row of white cars in a bright showroom"></div>
<div class="abs ph-taillight" role="img" aria-label="Close-up of a red car tail light"></div>
<div class="abs ph-silver" role="img" aria-label="Silver hatchback parked at sunset"></div>
<div class="abs ph-factory" role="img" aria-label="White cars on a factory production line"></div>
<div class="abs ph-blue" role="img" aria-label="Blue tinted close-up of a car body"></div>
<div class="abs dots" style="top:2296px"><span class="on"></span><span></span><span></span></div>

<!-- Testimonials -->
<section class="abs band band-reviews" role="img" aria-label="Green car hood covered in water droplets"></section>
<div class="on-green">
  <h2 class="abs title" style="top:2596px">What customers say</h2>
  <div class="abs subtitle" style="top:2634px">Testimonials</div>
  <div class="abs rule" style="top:2660px"></div>

  <article class="abs review" style="left:133px">
    <p>“ Fusce sollicitudin lorem et lectus volutpat. Proin placerat dapibus gravida. In tristique tristique nulla eget hendrerit. Maecenas vel tortor accumsan quam varius imperdiet vel eget elit. Aenean facilisis tincidunt lectus, id dictum nisl luctus eget. ”</p>
    <div class="reviewer"><div class="avatar" role="img" aria-label="Customer portrait"></div><div><b>Owen Marsh</b><small>City</small></div></div>
  </article>
  <article class="abs review" style="left:452px">
    <p>“ Sed tellus ex, imperdiet eget gravida sit amet, volutpat eget turpis. In nec ultricies est. Etiam mattis augue vehicula odio posuere, sit amet tempus lectus luctus. Nulla facilisis. Etiam vel massa elementum, bibendum tellus venenatis. ”</p>
    <div class="reviewer"><div class="avatar" role="img" aria-label="Customer portrait"></div><div><b>Delia</b><small>City</small></div></div>
  </article>
  <article class="abs review" style="left:771px">
    <p>“ Aliquam erat volutpat. Quisque aliquet ex nec est vestibulum pulvinar. Pellentesque convallis molestie enim sit amet efficitur. Etiam sit imperdiet lectus. Vivamus iaculis justo, ultrices nec erat in, euismod iaculis mauris. ”</p>
    <div class="reviewer"><div class="avatar" role="img" aria-label="Customer portrait"></div><div><b>Marcus</b><small>City</small></div></div>
  </article>

  <div class="abs dots" style="top:2964px"><span class="on"></span><span></span><span></span></div>
</div>

<!-- Contact form -->
<h2 class="abs title" style="top:3194px">Contact us</h2>
<div class="abs subtitle" style="top:3232px">Duis hendrerit arcu</div>
<div class="abs rule" style="top:3258px"></div>
<div class="abs field" style="left:133px;top:3298px;width:218px">Name</div>
<div class="abs field" style="left:373px;top:3298px;width:218px">Email</div>
<div class="abs field" style="left:610px;top:3298px;width:220px">Phone</div>
<div class="abs field" style="left:850px;top:3298px;width:217px">Car make and model</div>
<div class="abs field" style="left:133px;top:3360px;width:934px;height:43px">Message</div>
<div class="abs btn submit">Submit</div>

<!-- Contact info -->
<section class="abs band-dark" role="img" aria-label="Dark monochrome photo of a car interior"></section>
<h2 class="abs title" style="top:3704px;color:var(--white)">Contact info</h2>
<div class="abs subtitle" style="top:3742px;color:#9a9a9a">Pellentesque vehicula</div>
<div class="abs rule" style="top:3768px;background:var(--white)"></div>
<div class="abs info-row">
  <div><svg width="14" height="18" viewBox="0 0 14 18"><path fill="#fff" d="M7 0a7 7 0 0 0-7 7c0 5 7 11 7 11s7-6 7-11a7 7 0 0 0-7-7zm0 9.5A2.5 2.5 0 1 1 7 4.5a2.5 2.5 0 0 1 0 5z"/></svg>24 Building name, Street name, City - Zipcode</div>
  <div><svg width="16" height="16" viewBox="0 0 24 24"><path fill="#fff" d="M6.6 10.8a15 15 0 0 0 6.6 6.6l2.2-2.2c.3-.3.7-.4 1-.2 1.1.4 2.3.6 3.6.6.6 0 1 .4 1 1V20c0 .6-.4 1-1 1A17 17 0 0 1 3 4c0-.6.4-1 1-1h3.5c.6 0 1 .4 1 1 0 1.3.2 2.5.6 3.6.1.3 0 .7-.2 1z"/></svg>555 132 0199</div>
  <div><svg width="16" height="12" viewBox="0 0 16 12"><rect width="16" height="12" rx="1" fill="#fff"/><path d="m1 1 7 6 7-6" stroke="#333" stroke-width="1.5" fill="none"/></svg>info@verdanttint.com</div>
</div>
<div class="abs social-row"><span></span><span></span><span></span><span></span><span></span><span></span></div>

<!-- Footer -->
<div class="abs footer-links">Home<span>|</span>Window Film Services<span>|</span>Film<span>|</span>About<span>|</span>Gallery<span>|</span>Contact</div>
<div class="abs copyright">Copyright © 2017 Verdant Tint. All rights reserved.</div>

</body>
</html>
```